New Flyer Design Project

I have an Upmarket Hair and Beauty Salon near the beach. I already have a current logo but it needs to change to Hair AND Beauty as we were only doing beauty. I want it to have a special on the flyer and to be DL size. I like it to be elegant with soft colours. I like the blues/teals also. I have attached the current business cards. I want it to tie in with the business cards somehow as well. I want the add to have something along the lines of - Marnie & Tess now introduce to you Hair AND Beauty. We have combined our team to offer you all of your hair and beauty needs in the one great location! NEW CLIENTS OFFER $49 Style Cut & Blowdry and 30% off ALL Waxing

We are a Velunique and Solvadermix Salon so you can google to get the feel of the brand. The flyer will be used as a leaflet drop.
Please include an expiry of march 31st 2015
I would prefer not to use stock images also
Phone Number 08 9473 2804
shop 4&5 Corrow Point Pde
Yanchep 6035

Thankyou :)

Target Market(s)

20-40

Industry/Entity Type

Hair

Requirements
Must have
• DL size
Address & Contact details
08 9473 2804
shop 4&5 Corrow Point Pde
Corrow Bay 6081
Should not have
• Do not like clip arts-scissors etc
Would prefer not to use stock images

```html
<!DOCTYPE html>
<html lang="en">
<head>
<meta charset="utf-8">
<title>Marnie &amp; Tess – Hair &amp; Beauty Flyer</title>
<link rel="stylesheet" href="https://fonts.googleapis.com/css2?family=Open+Sans:wght@400;600;700&family=Great+Vibes&display=swap">
<style>
  :root {
    --page: #ffffff;
    --frame: #000000;
    --teal-top: #4ff0c6;
    --teal-bottom: #20b7a5;
    --teal-label: #4ee8c4;
    --wood-dark: #140d09;
    --wood-mid: #3a2a20;
    --plate-bg: #ffffff;
    --plate-edge: #c9b8a6;
    --plate-ink: #5a3f2a;
    --text-light: #ffffff;
    --photo-light: #e9e9e9;
    --photo-mid: #8c8c8c;
    --photo-dark: #2a2a2a;
  }
  * { box-sizing: border-box; margin: 0; padding: 0; }
  html, body { width: 1200px; height: 2309px; overflow: hidden; background: var(--page); }
  .flyer { position: relative; width: 1200px; height: 2309px; font-family: "Open Sans", Arial, sans-serif; }
  .frame { position: absolute; left: 90px; top: 81px; width: 1028px; height: 2160px; background: var(--frame); }
  .hero-photo {
    position: absolute; left: 171px; top: 166px; width: 866px; height: 981px;
    background: radial-gradient(ellipse at 60% 60%, var(--photo-light) 0%, var(--photo-mid) 45%, var(--photo-dark) 100%);
  }
  .brand-band {
    position: absolute; left: 90px; top: 1147px; width: 1028px; height: 266px;
    background: repeating-linear-gradient(180deg, var(--wood-dark) 0px, var(--wood-mid) 3px, var(--wood-dark) 7px);
  }
  .brand-plate {
    position: absolute; left: 265px; top: 1202px; width: 678px; height: 161px;
    background: var(--plate-bg); border: 2px solid var(--plate-edge);
    display: flex; flex-direction: column; align-items: center; justify-content: center;
    color: var(--plate-ink);
  }
  .brand-name { font-weight: 400; font-size: 64px; line-height: 1; }
  .brand-tagline { font-weight: 400; font-size: 28px; margin-top: 12px; }
  .offer-panel {
    position: absolute; left: 171px; top: 1413px; width: 866px; height: 747px;
    background: linear-gradient(180deg, var(--teal-top), var(--teal-bottom));
    color: var(--text-light); text-align: center;
  }
  .intro-line { position: absolute; left: 0; right: 0; top: 8px; font-size: 35px; line-height: 1.2; padding-left: 90px; }
  .intro-line strong { font-weight: 700; }
  .intro-script { position: absolute; left: 0; right: 0; top: 58px; font-family: "Great Vibes", cursive; font-size: 96px; line-height: 1; letter-spacing: 4px; }
  .intro-copy { position: absolute; left: 0; right: 0; top: 208px; font-size: 25px; line-height: 1.5; }
  .intro-copy strong { font-weight: 700; }
  .deal-box {
    position: absolute; left: 90px; top: 310px; width: 686px; height: 206px;
    background: var(--frame); padding-top: 14px;
  }
  .deal-label { color: var(--teal-label); font-weight: 700; font-size: 26px; letter-spacing: 1px; line-height: 1.3; }
  .deal-item { font-weight: 700; font-size: 37px; line-height: 1.32; }
  .deal-expiry { font-size: 21px; margin-top: 2px; }
  .contact-phone { position: absolute; left: 0; right: 0; top: 540px; font-weight: 700; font-size: 46px; line-height: 1.2; }
  .contact-address { position: absolute; left: 0; right: 0; top: 606px; font-size: 38px; line-height: 1.2; }
  .contact-email { position: absolute; left: 0; right: 0; top: 659px; font-size: 25px; line-height: 1.2; }
</style>
</head>
<body>
<div class="flyer">
  <div class="frame"></div>
  <div class="hero-photo" role="img" aria-label="Black and white portrait photograph of a woman with long sweeping hair"></div>
  <div class="brand-band"></div>
  <div class="brand-plate">
    <div class="brand-name">Marnie &amp; Tess</div>
    <div class="brand-tagline">Your salon by the sea</div>
  </div>
  <section class="offer-panel">
    <p class="intro-line">Now <strong>Introduce</strong> To You</p>
    <p class="intro-script">Hair &amp; Beauty</p>
    <p class="intro-copy">We have combined our team to offer you all of your<br><strong>hair and beauty needs in the one great location</strong>!</p>
    <div class="deal-box">
      <p class="deal-label">NEW CLIENTS OFFER</p>
      <p class="deal-item">$49 Style Cut &amp; Blow Dry</p>
      <p class="deal-item">30% off ALL Waxing</p>
      <p class="deal-expiry">valid till march 31st 2015</p>
    </div>
    <p class="contact-phone">08 9473 2804</p>
    <p class="contact-address">shop 4&amp;5 Corrow Point Pde Corrow Bay 6081</p>
    <p class="contact-email">marnie.tess.beauty@mailbox.com</p>
  </section>
</div>
</body>
</html>
```